Willow Cradle Pregnancy and Baby Massage

I need a web design for a new business, WILLOW CRADLE PREGNANCY AND BABY MASSAGE that I am in the process of setting up in the suburbs of Perth, Western Australia. The business is owned and operated by myself and my intention is to service Pregnant Mothers and Parents of Young Babies that would benefit from massage. I would like to have a "Home Page" and pages for "About Me", "Pregnancy Massage", "Baby Massage", a Pricing Page for Pregnancy Massage Sessions, a Pricing Page for Baby Massage Sessions, and a "Contact Me" page to allow clients to either contact me with queries or book available pregnancy massage sessions on a particular day of the week. I would also like a "News" page that would include articles I have written, news about new courses and a link to my Facebook page (yet to be set up). I would like to keep the colour schemes similar to my logo design colours. I need the design to be easy to follow and to appeal to a younger audience (20's to mid 30's).
The target audience is pregnant mothers-to-be wishing to receive massage treatments, and new parents and grandparents of small babies that would like to learn how to massage their babies.
The look and feel should be modern, professional, elegant and feminine.
I need the design to be in a standard format such that I can update the content by myself ( and does not need specialised software) as the company and business progresses.

Target Market(s)

Contact Information for Business Card

Card should have rounded edges. Design should have the same "feel" as the website. Contact Details of my business address, mobile phone, email and website should be included.

Font styles to use
Script

Requirements
Must have
• Same colours as logo design. In cmyk system, the colours are: 20,60,0,0 which best result is pantone 681 and 40,40,0,0 which best result is pantone 2645. Card should include the logo design.

```html
<!DOCTYPE html>
<html lang="en">
<head>
<meta charset="utf-8">
<title>Willow Cradle Pregnancy and Baby Massage</title>
<link rel="stylesheet" href="https://fonts.googleapis.com/css2?family=Lato:wght@400;700;900&family=PT+Sans:wght@400;700&family=Great+Vibes&display=swap">
<style>
:root{
  --orchid:#b86fa3;
  --orchid-deep:#a35a90;
  --rose-script:#b45f9d;
  --ink:#2d2846;
  --text:#4a4a4a;
  --line:#cfcfcf;
  --lavender:#f4f2f8;
  --night:#3b3052;
  --white:#ffffff;
}
*{box-sizing:border-box;margin:0;padding:0}
html,body{width:1200px;height:3098px;overflow:hidden;background:var(--white)}
body{position:relative;font-family:"PT Sans",Arial,sans-serif;color:var(--text)}
.abs{position:absolute}

/* header */
.brand{left:76px;top:18px;display:flex;align-items:center;gap:12px}
.brand-dot{width:34px;height:34px;border-radius:50%;background:var(--orchid)}
.brand-name{font-family:"PT Sans",Arial,sans-serif;font-weight:700;font-size:17px;line-height:1.2;color:var(--orchid-deep);width:170px}
.nav{top:52px;left:350px;right:0;height:20px}
.nav a{font-family:"PT Sans",Arial,sans-serif;font-size:13px;letter-spacing:.5px;color:#9a9a9a;text-decoration:none;text-transform:uppercase;position:absolute;top:0;white-space:nowrap;line-height:16px}
.nav a.current{color:var(--ink);border:2px solid var(--orchid);padding:13px 26px;top:-15px}

/* hero */
.hero-title{left:78px;top:198px;font-family:"Lato",Arial,sans-serif;font-weight:700;font-size:38px;line-height:48px;color:var(--ink);white-space:nowrap}
.hero-title b{font-weight:900;color:#111}
.btn{display:flex;align-items:center;justify-content:center;border:2px solid var(--ink);font-family:"PT Sans",Arial,sans-serif;font-size:19px;color:#111;background:transparent}
.btn-hero{left:78px;top:368px;width:186px;height:52px;border-color:var(--orchid)}
.hero-photo{left:560px;top:124px;width:640px;height:403px;background:radial-gradient(ellipse at 55% 55%,#f3d9c9 0%,#f8ebe3 45%,#ffffff 75%)}

/* about */
.about{left:0;top:562px;width:1200px;height:371px;background:var(--orchid)}
.script-title{font-family:"Great Vibes",cursive;font-weight:400;color:#111;text-align:center;position:absolute;left:0;width:100%;line-height:1.1}
.about .script-title{top:48px;font-size:60px}
.about-copy{position:absolute;left:100px;width:1000px;top:122px;font-size:13.5px;line-height:20px;color:#2a1f2a;text-align:center}
.about-copy p+p{margin-top:20px}
.btn-about{left:506px;top:268px;width:186px;height:50px}

/* story grid */
.story-box{left:78px;top:985px;width:498px;height:341px;border:1px solid var(--line);padding:0 32px;display:flex;align-items:center}
.story-box p{font-family:Arial,sans-serif;font-size:16px;line-height:26px;color:#666}
.photo-twins-a{left:624px;top:985px;width:497px;height:248px;background:linear-gradient(135deg,#8a6a5c,#d9a08b 45%,#e9c2b0 70%,#6f5a52)}
.photo-twins-b{left:78px;top:1359px;width:498px;height:248px;background:linear-gradient(135deg,#6b5344,#b0917a 45%,#d8b6a4 70%,#7f6a5b)}
.vision{left:624px;top:1266px;width:497px;height:341px;background:var(--orchid);padding:46px 34px 0;font-family:Arial,sans-serif;font-size:15.5px;line-height:25px;color:var(--white)}
.vision p+p{margin-top:25px}

/* services */
.services{left:0;top:1669px;width:1200px;height:733px;background:var(--lavender)}
.services .script-title{top:50px;font-size:60px}
.service{position:absolute;top:138px;width:400px;text-align:center}
.service-photo{width:289px;height:289px;border-radius:50%;margin:0 auto;border:2px solid #e4dfe8}
.photo-pregnancy{background:radial-gradient(circle at 50% 45%,#c8926c,#7a4a32 60%,#3e2a20)}
.photo-baby{background:radial-gradient(circle at 50% 50%,#f6dccb,#efc7b0 55%,#f7f3f1)}
.service h3{font-family:"Great Vibes",cursive;font-weight:400;font-size:46px;color:var(--rose-script);margin-top:16px;line-height:56px}
.service p{font-size:16px;line-height:25px;color:#666;margin:12px auto 0;width:365px;height:75px}
.service .btn{width:186px;height:52px;margin:28px auto 0}

/* enquiry */
.enquiry{left:0;top:2402px;width:1200px;height:386px;background:var(--orchid)}
.enquiry .script-title{top:42px;font-size:58px}
.field{position:absolute;border:1.5px solid #5a3b56;font-size:14px;color:#3a2638;padding:10px 20px}
.btn-submit{left:514px;top:282px;width:186px;height:52px}

/* footer */
.foot-col{position:absolute;top:2826px}
.foot-col h4{font-family:"Great Vibes",cursive;font-weight:400;font-size:28px;color:#111;margin-bottom:14px;line-height:1.1}
.contact-row{display:flex;align-items:center;gap:14px;font-size:14px;line-height:20px;color:#333;margin-bottom:18px;width:300px}
.contact-row svg{flex:none}
.post{display:flex;gap:12px;margin-bottom:12px;width:340px}
.post-thumb{flex:none;width:52px;height:52px;border-radius:50%;background:radial-gradient(circle,#e1b69b,#8c5a45)}
.post p{font-size:13.5px;line-height:18px;color:#333}
.post small{display:block;font-size:12px;color:#999;margin-top:4px}
.news-copy{font-size:13.5px;line-height:19px;color:#333;width:300px}
.news-form{display:flex;margin-top:22px;width:318px;height:50px;border:1px solid #ddd}
.news-form span{flex:1;font-style:italic;font-size:13px;color:#aaa;padding:16px 20px}
.news-form b{width:52px;background:var(--orchid);display:flex;align-items:center;justify-content:center}

.bottom-bar{left:0;top:3036px;width:1200px;height:62px;background:var(--night);display:flex;align-items:center;padding:0 76px;justify-content:space-between}
.bottom-bar p{font-size:13px;font-weight:700;color:var(--white)}
.socials{display:flex;gap:22px}
.socials i{width:14px;height:14px;border-radius:50%;background:#9c94b0;display:block}
</style>
</head>
<body>

<header>
  <div class="abs brand">
    <span class="brand-dot"></span>
    <span class="brand-name">Willow Cradle Pregnancy and Baby Massage</span>
  </div>
  <nav class="abs nav">
    <a class="current" style="left:0">Home</a>
    <a style="left:121px">About Me</a>
    <a style="left:251px">Pregnancy Massage</a>
    <a style="left:455px">Baby Massage</a>
    <a style="left:606px">Pricing</a>
    <a style="left:711px">Contact</a>
  </nav>
</header>

<section class="hero">
  <h1 class="abs hero-title">Support for <b>YOU</b> and <b>YOUR BABY</b><br>through <b>PREGNANCY</b> and<br><b>CHILD BIRTH</b></h1>
  <div class="abs btn btn-hero">Contact Us Now</div>
  <div class="abs hero-photo" role="img" aria-label="Photo of a smiling baby lying on its back receiving a gentle massage"></div>
</section>

<section class="abs about">
  <h2 class="script-title">About Me</h2>
  <div class="about-copy">
    <p>Maren is a Practitioner of Pregnancy Massage, and a Paediatric Massage Consultant. She completed her training with Prenatal Touch Academy, and the Infant Touch Learning Network. The ITLN is endorsed by the National College of Midwifery Practice. The Natural Therapies Council, and accredited by the Guild of Massage Practitioners.</p>
    <p>Maren is also a Registered Nurse and Midwife. Most of her professional career has been as a midwife, which has included working in the community in the UK, providing ante natal care and classes, intra partum care, home births, and postnatal care in the home.</p>
  </div>
  <div class="abs btn btn-about">Read More</div>
</section>

<section class="story">
  <div class="abs story-box"><p>Willow Cradle Pregnancy and Baby Massage was launched in 2017, offering massage for pregnant women, and instruction of baby massage to parents, grandparents and carers.</p></div>
  <div class="abs photo-twins-a" role="img" aria-label="Photo of two newborn twins sleeping together on a soft peach wrap"></div>
  <div class="abs photo-twins-b" role="img" aria-label="Photo of two newborn babies curled up in a fur-lined basket"></div>
  <div class="abs vision">
    <p>My vision is to provide a professional massage service to pregnant mothers and babies that also benefits from my skills and experience as a midwife.</p>
    <p>My expectation is that after each session, my clients should leave feeling relaxed, calm, emotionally nurtured, soothed.</p>
    <p>At all times, I will take the utmost care of your privacy, safety and comfort in what is a very personal, intimate time in your life.</p>
  </div>
</section>

<section class="abs services">
  <h2 class="script-title">My Services</h2>
  <div class="service" style="left:190px">
    <div class="service-photo photo-pregnancy" role="img" aria-label="Photo of a pregnant woman lying on her side receiving a massage"></div>
    <h3>Pregnancy Massage</h3>
    <p>Pregnancy massage is the prenatal use of massage therapy to support the physiological, structural and emotional wellbeing of both mother and baby.</p>
    <div class="btn">Read More</div>
  </div>
  <div class="service" style="left:610px">
    <div class="service-photo photo-baby" role="img" aria-label="Photo of a baby lying on its tummy having its back massaged"></div>
    <h3>Baby Massage</h3>
    <p>This class teaches parents and carers the brief basics of Baby massage so they can get started at home.</p>
    <div class="btn">Read More</div>
  </div>
</section>

<section class="abs enquiry">
  <h2 class="script-title">Getting more info about Us</h2>
  <div class="field" style="left:219px;top:130px;width:289px;height:46px">Name:</div>
  <div class="field" style="left:219px;top:181px;width:289px;height:46px">Phone:</div>
  <div class="field" style="left:219px;top:233px;width:289px;height:46px">E-Mail:</div>
  <div class="field" style="left:514px;top:130px;width:467px;height:149px">Message:</div>
  <div class="abs btn btn-submit">Submit</div>
</section>

<footer>
  <div class="foot-col" style="left:76px">
    <h4>Contact Info</h4>
    <div class="contact-row">
      <svg width="22" height="28" viewBox="0 0 22 28" fill="none" stroke="#b86fa3" stroke-width="1.6"><path d="M11 26C11 26 2 16 2 10a9 9 0 0 1 18 0c0 6-9 16-9 16z"/><circle cx="11" cy="10" r="3.2"/></svg>
      <span>123 Building Name, Street Name, City, Country - zipcode</span>
    </div>
    <div class="contact-row">
      <svg width="22" height="22" viewBox="0 0 22 22" fill="none" stroke="#b86fa3" stroke-width="1.6"><path d="M5 2l4 4-2.5 2.5a12 12 0 0 0 7 7L16 13l4 4-3 3C9 20 2 13 2 5z"/></svg>
      <span>0400 555 218</span>
    </div>
    <div class="contact-row">
      <svg width="22" height="16" viewBox="0 0 22 16" fill="none" stroke="#b86fa3" stroke-width="1.6"><rect x="1" y="1" width="20" height="14"/><path d="M1 1l10 8 10-8"/></svg>
      <span>maren.ellis@willow-cradle.com.au</span>
    </div>
  </div>
  <div class="foot-col" style="left:430px">
    <h4>Blog Post</h4>
    <div class="post"><div class="post-thumb" role="img" aria-label="Thumbnail photo of a baby massage"></div><p>Lorem Ipsum is simply dummy text of the printing and typesetting industry.<small>Sep 12, 2017</small></p></div>
    <div class="post"><div class="post-thumb" role="img" aria-label="Thumbnail photo of a baby massage"></div><p>Lorem Ipsum is simply dummy text of the printing and typesetting industry.<small>Sep 12, 2017</small></p></div>
  </div>
  <div class="foot-col" style="left:805px">
    <h4>Newsletter</h4>
    <p class="news-copy">Lorem Ipsum is simply dummy text of the printing and typesetting industry.</p>
    <div class="news-form"><span>Type Here...</span><b><svg width="24" height="18" viewBox="0 0 24 18" fill="none" stroke="#fff" stroke-width="1.6"><rect x="1" y="1" width="22" height="16"/><path d="M1 1l11 9 11-9"/></svg></b></div>
  </div>
  <div class="abs bottom-bar">
    <p>© Willow Cradle - 2017.All Rights Reserved.</p>
    <div class="socials"><i></i><i></i><i></i><i></i></div>
  </div>
</footer>

</body>
</html>
```